Animal Eye Clinic needs a Business card

We are a new veterinary ophthalmology practice (Ridgeline Pet Vision Care) and we need a business card designed. We only see animal eyes - we are not a regular veterinary clinic. We already have a logo. We are looking for a professional, good looking business card to hand out to our clients. We are looking for something simple but professional and contemporary. Our logo is likely the only picture/graphic that needs to be on the card.
Updates

Contact Information for Business Card

Delia Vossman, BSc, DVM, MSc, DipACVO
Veterinary Ophthalmologist

Phone: 250.418.3927
Email: ridgelinepetvisioncare@mailbox-example.net
Website: ridgelinepetvisioncare-example.net
Address: 1874 Thornbury Rd
Kelowna, BC, V1X 4M9

Colors

Designer to choose colors to be used in the design.

Requirements
Must have
• Our logo (attached)

```html
<!DOCTYPE html>
<html lang="en">
<head>
<meta charset="utf-8">
<title>Ridgeline Pet Vision Care – Business Card</title>
<link href="https://fonts.googleapis.com/css2?family=Montserrat:wght@400;700&family=Questrial&display=swap" rel="stylesheet">
<style>
  :root {
    --bg: #e9e7e4;
    --card-white: #f7f7f7;
    --card-grey: #747474;
    --teal: #1b97a6;
    --ink-grey: #6f6f6f;
    --text-light: #8a8a8a;
    --white: #ffffff;
  }
  * { margin: 0; padding: 0; box-sizing: border-box; }
  html, body {
    width: 1200px; height: 900px; overflow: hidden;
    background: var(--bg);
  }
  .canvas {
    position: relative; width: 1200px; height: 900px;
  }
  .card {
    position: absolute; left: 267px; width: 665px; height: 380px;
    box-shadow: 0 6px 18px rgba(0,0,0,.15);
    overflow: hidden;
  }
  .card--front { top: 45px; background: var(--card-white); }
  .card--back { top: 475px; background: var(--card-grey); }

  /* front */
  .side-tab {
    position: absolute; left: -10px; top: 62px; width: 26px; height: 66px;
    background: var(--card-grey); border-radius: 8px;
  }
  .identity { position: absolute; left: 44px; top: 48px; }
  .identity__name {
    font-family: "Montserrat", sans-serif; font-size: 31px; letter-spacing: 5px;
    line-height: 1; text-transform: uppercase;
  }
  .identity__first { color: var(--teal); font-weight: 700; }
  .identity__last { color: var(--ink-grey); font-weight: 400; }
  .identity__role, .identity__creds {
    font-family: "Montserrat", sans-serif; font-size: 14px; letter-spacing: 1.2px;
    color: var(--ink-grey); text-transform: uppercase; line-height: 1.3;
  }
  .identity__role { margin-top: 4px; }

  .contact-list {
    position: absolute; right: 36px; top: 116px; list-style: none;
    font-family: "Questrial", sans-serif; font-size: 13px; letter-spacing: 1.3px;
    color: var(--text-light); text-align: right;
  }
  .contact-list li {
    display: flex; align-items: center; justify-content: flex-end;
    gap: 12px; height: 30px;
  }
  .contact-icon {
    width: 22px; height: 22px; border-radius: 5px; background: var(--teal);
    display: flex; align-items: center; justify-content: center; flex: none;
  }
  .contact-icon svg { width: 13px; height: 13px; }

  .brand-mark {
    position: absolute; left: 60px; bottom: 60px;
    display: flex; align-items: center; gap: 14px;
  }
  .brand-mark__dot {
    width: 58px; height: 58px; border-radius: 50%; background: var(--teal); flex: none;
  }
  .brand-mark__name {
    font-family: "Montserrat", sans-serif; font-weight: 700; font-size: 18px;
    letter-spacing: 1.5px; color: var(--teal); text-transform: uppercase; line-height: 1.25;
    max-width: 240px;
  }

  /* back */
  .back-brand {
    position: absolute; left: 0; right: 0; top: 118px;
    display: flex; align-items: center; justify-content: center; gap: 22px;
  }
  .back-brand__dot {
    width: 82px; height: 82px; border-radius: 50%; background: var(--white); flex: none;
  }
  .back-brand__name {
    font-family: "Montserrat", sans-serif; font-weight: 700; font-size: 30px;
    letter-spacing: 2px; color: var(--white); text-transform: uppercase; line-height: 1.15;
    max-width: 360px;
  }
  .back-web {
    position: absolute; left: 0; right: 0; bottom: 58px; text-align: center;
    font-family: "Questrial", sans-serif; font-size: 19px; letter-spacing: 3px;
    color: var(--white);
  }
</style>
</head>
<body>
<main class="canvas">
  <section class="card card--front" aria-label="Business card front">
    <div class="side-tab"></div>
    <div class="identity">
      <h1 class="identity__name"><span class="identity__first">Delia</span> <span class="identity__last">Vossman</span></h1>
      <p class="identity__role">Veterinary Ophthalmologist</p>
      <p class="identity__creds">BSc, DVM, MSc, DipACVO</p>
    </div>

    <ul class="contact-list">
      <li>250.418.3927
        <span class="contact-icon"><svg viewBox="0 0 24 24"><path fill="#fff" d="M6.6 10.8a15 15 0 0 0 6.6 6.6l2.2-2.2c.3-.3.7-.4 1-.2 1.1.4 2.3.6 3.6.6.6 0 1 .4 1 1V20c0 .6-.4 1-1 1A17 17 0 0 1 3 4c0-.6.4-1 1-1h3.5c.6 0 1 .4 1 1 0 1.2.2 2.4.6 3.6.1.3 0 .7-.2 1z"/></svg></span></li>
      <li>1874 Thornbury Rd Kelowna, BC, V1X 4M9
        <span class="contact-icon"><svg viewBox="0 0 24 24"><path fill="#fff" d="M12 2a7 7 0 0 0-7 7c0 5 7 13 7 13s7-8 7-13a7 7 0 0 0-7-7zm0 9.5A2.5 2.5 0 1 1 12 6.5a2.5 2.5 0 0 1 0 5z"/></svg></span></li>
      <li>ridgelinepetvisioncare@mailbox-example.net
        <span class="contact-icon"><svg viewBox="0 0 24 24"><path fill="#fff" d="M2 11 22 3l-5 18-5-7-6 4 2-6z"/></svg></span></li>
      <li>ridgelinepetvisioncare-example.net
        <span class="contact-icon"><svg viewBox="0 0 24 24" fill="none" stroke="#fff" stroke-width="2"><circle cx="12" cy="12" r="9"/><path d="M3 12h18M12 3c3 3 3 15 0 18M12 3c-3 3-3 15 0 18"/></svg></span></li>
    </ul>

    <div class="brand-mark">
      <span class="brand-mark__dot"></span>
      <span class="brand-mark__name">Ridgeline Pet Vision Care</span>
    </div>
  </section>

  <section class="card card--back" aria-label="Business card back">
    <div class="back-brand">
      <span class="back-brand__dot"></span>
      <span class="back-brand__name">Ridgeline Pet Vision Care</span>
    </div>
    <p class="back-web">ridgelinepetvisioncare-example.net</p>
  </section>
</main>
</body>
</html>
```